Tandem Hearth Works Pty Ltd

We need business cards for a company based in Perth, we install, service and maintain fire equipment.
On the front we want a great design with our logo and a small spot for our full company name, general company email address and office number. On the back we need space for our name, title, mobile number and email address on the back.

Target Market(s)

Facility managers and commercial/industrial building owners/occupiers.

Contact Information for Business Card

Font styles to use
Sans Serif

Requirements
Must have
• Please only submit 5 of your best samples.
Darker tones are preferred.
Nice to have
• We want to use, black, red and grey. Keep it modern and clean.
I've attached the company logo and a sample of a boarder we use on our emergency plans.
Should not have
• No preference. Let the designer choose.

```html
<!DOCTYPE html>
<html lang="en">
<head>
<meta charset="utf-8">
<title>Tandem Hearth Works – Business Cards</title>
<link href="https://fonts.googleapis.com/css2?family=Montserrat:wght@700;800&family=Arimo:wght@400;700&display=swap" rel="stylesheet">
<style>
  :root {
    --fire-red: #ec1c24;
    --card-white: #ffffff;
    --ink: #222222;
    --rule-light: rgba(255,255,255,0.45);
    --rule-grey: #c8c8c8;
    --stage: #2b2b2b;
  }
  * { margin: 0; padding: 0; box-sizing: border-box; }
  html, body {
    width: 1200px; height: 1040px; overflow: hidden;
    background: var(--stage);
  }
  .stage {
    position: relative; width: 1200px; height: 1040px;
    display: flex; flex-direction: column; align-items: center; justify-content: center; gap: 60px;
  }
  .card {
    position: relative; width: 600px; height: 343px;
    display: flex; align-items: center;
    padding: 0 44px 0 48px;
  }
  .card--front {
    background: var(--fire-red); color: var(--card-white);
    border-radius: 70px 0 70px 0;
  }
  .card--back {
    background: var(--card-white); color: var(--ink);
    border-radius: 0 70px 0 70px;
  }
  .brand {
    width: 220px; flex-shrink: 0;
    font-family: "Montserrat", sans-serif; font-weight: 800;
    font-size: 30px; line-height: 1.05; letter-spacing: 0.5px;
    text-transform: uppercase;
  }
  .card--back .brand { color: var(--fire-red); }
  .divider {
    width: 1px; height: 120px; margin: 0 34px 0 20px; flex-shrink: 0;
    background: var(--rule-light);
  }
  .card--back .divider { background: var(--rule-grey); }
  .details { font-family: "Arimo", sans-serif; }
  .company {
    font-family: "Montserrat", sans-serif; font-weight: 800;
    font-size: 16px; line-height: 1.15; letter-spacing: 0.6px;
    text-transform: uppercase;
  }
  .office-phone {
    font-family: "Montserrat", sans-serif; font-weight: 800;
    font-size: 21px; margin: 8px 0 10px; letter-spacing: 0.5px;
  }
  .person {
    font-family: "Montserrat", sans-serif; font-weight: 800;
    font-size: 20px; color: var(--fire-red); letter-spacing: 0.6px;
    text-transform: uppercase;
  }
  .role { font-size: 17px; margin: 2px 0 16px; }
  .contact-line {
    display: flex; align-items: center; gap: 9px;
    font-size: 14px; line-height: 1.55; letter-spacing: 0.3px;
  }
  .card--back .contact-line { font-size: 17px; }
  .icon { width: 16px; height: 16px; flex-shrink: 0; }
  .card--back .icon { width: 18px; height: 18px; }
</style>
</head>
<body>
<main class="stage">
  <section class="card card--front" aria-label="Card front">
    <div class="brand">Tandem<br>Hearth<br>Works</div>
    <div class="divider"></div>
    <div class="details">
      <p class="company">Tandem Hearth<br>Works Pty Ltd</p>
      <p class="office-phone">789.555.0142</p>
      <p class="contact-line">
        <svg class="icon" viewBox="0 0 16 16" fill="none" stroke="#fff" stroke-width="1.5"><rect x="1" y="3.5" width="14" height="9"/><path d="M1 3.5l7 5 7-5"/></svg>
        info@tandemhearth.com
      </p>
      <p class="contact-line">
        <svg class="icon" viewBox="0 0 16 16" fill="none" stroke="#fff" stroke-width="1.3"><circle cx="8" cy="8" r="6.5"/><ellipse cx="8" cy="8" rx="3" ry="6.5"/><path d="M1.5 8h13M2.5 5h11M2.5 11h11"/></svg>
        www.tandemhearth.com
      </p>
    </div>
  </section>

  <section class="card card--back" aria-label="Card back">
    <div class="brand">Tandem<br>Hearth<br>Works</div>
    <div class="divider"></div>
    <div class="details">
      <p class="person">Marcus Hale</p>
      <p class="role">Managing Director</p>
      <p class="contact-line">
        <svg class="icon" viewBox="0 0 16 16" fill="none" stroke="#ec1c24" stroke-width="1.6"><rect x="4" y="1" width="8" height="14" rx="1.5"/><circle cx="8" cy="12.3" r="0.6" fill="#ec1c24"/></svg>
        789.555.0187
      </p>
      <p class="contact-line">
        <svg class="icon" viewBox="0 0 16 16"><rect x="1" y="3.5" width="14" height="9" fill="#ec1c24"/><path d="M1 3.5l7 5 7-5" fill="none" stroke="#fff" stroke-width="1.2"/></svg>
        marcus@tandemhearth.com
      </p>
    </div>
  </section>
</main>
</body>
</html>
```